Bramblewick Homes Tarrow Customer Brochure

Need a brochure designed that is clean and minimal that contains our logo, and contact information. Would like an area where we could insert business cards, and slips on both sides of the openings to place sheets of paper in. Would prefer to have the COVER LETTER I have attached printed on one side of the opening.

Target Market(s)

Home buyers

Font styles to use
Sans Serif

Colors

Designer to choose colors to be used in the design.

Requirements
Must have
• Logo, contact info, website, etc. Must be minimal in design and very clean looking.
Nice to have
• Please see above
Should not have
• No stock pictures of homes, builds, etc. Need it to look very clean

```html
<!DOCTYPE html>
<html lang="en">
<head>
<meta charset="utf-8">
<title>Bramblewick Homes Tarrow – Brochure</title>
<link href="https://fonts.googleapis.com/css2?family=Lato:wght@400;700&family=Roboto+Condensed:wght@400;700&display=swap" rel="stylesheet">
<style>
:root{
  --stage:#cccccc;
  --tan:#d2a679;
  --tan-light:#e6c9a8;
  --ink:#2f2d2e;
  --paper:#ffffff;
  --muted:#555;
  --rule:#e8c9a6;
}
*{box-sizing:border-box;margin:0;padding:0}
html,body{width:1200px;height:1200px;overflow:hidden}
body{background:var(--stage);font-family:"Lato",sans-serif;color:var(--ink);position:relative}
.view-label{position:absolute;font-size:29px;color:#222;transform:translateX(-50%);white-space:nowrap;font-family:"Lato",sans-serif}
.sheet{position:absolute;background:var(--paper);overflow:hidden;box-shadow:4px 5px 6px rgba(0,0,0,.25)}
.sheet svg.deco{position:absolute;inset:0;width:100%;height:100%}
.panel-tan{position:absolute;top:0;bottom:0;left:0;background:var(--tan)}
.brand{font-family:"Roboto Condensed",sans-serif;text-align:center;color:var(--ink);position:absolute}
.brand .mark{display:block;margin:0 auto 6px;background:var(--ink)}
.brand .name{font-weight:700;display:block;line-height:1;letter-spacing:.2px}
.brand .sub{font-weight:400;display:block;letter-spacing:4px;line-height:1.1}
.contact{position:absolute;color:#fff;font-weight:700;font-size:7.4px;text-align:center}
.contact li{list-style:none;margin-bottom:4px}
.contact svg{display:block;margin:0 auto 2px;width:8px;height:8px}
.socials{display:flex;gap:10px;justify-content:center;margin-top:10px}
.socials span{width:13px;height:13px;border-radius:50%;background:#fff;display:block}
.letter{position:absolute;left:24px;top:30px;width:290px;color:#fff;font-size:7.4px;line-height:10.1px;text-align:justify}
.signoff{position:absolute;left:194px;top:286px;color:#fff;font-family:"Roboto Condensed",sans-serif;font-weight:700;font-size:8px;line-height:11px}
.back-contact{position:absolute;left:176px;top:390px;color:#fff;font-size:7px;line-height:16px}
.back-contact li,.inside-contact li{list-style:none;display:flex;align-items:flex-start;gap:6px}
.back-contact svg,.inside-contact svg{width:7px;height:7px;margin-top:4px;flex:none}
.pocket-card{position:absolute;left:360px;top:377px;width:136px;height:70px;background:#f2f2f2;display:flex;align-items:center;justify-content:center;font-size:7.5px;color:#333;box-shadow:0 1px 3px rgba(0,0,0,.4)}
.profile-title{position:absolute;top:100px;left:0;right:0;text-align:center;font-family:"Roboto Condensed",sans-serif;font-size:21px}
.profile-title b{font-weight:700}
.profile-title span{color:#777}
.profile-body{position:absolute;left:24px;top:130px;width:278px;font-size:4.6px;line-height:5.6px;color:#333;text-align:justify}
.profile-body strong{display:block;margin-bottom:6px;font-family:"Roboto Condensed",sans-serif}
.inside-contact{position:absolute;left:24px;top:266px;font-size:4.6px;line-height:11px;color:#333}
.inside-contact svg{margin-top:2px}
</style>
</head>
<body>

<div class="view-label" style="left:382px;top:40px">front side of the brouchure</div>
<div class="view-label" style="left:382px;top:616px">back side of the brouchure</div>
<div class="view-label" style="left:974px;top:616px">inside of the brouchure</div>

<!-- Front -->
<section class="sheet front" style="left:42px;top:102px;width:648px;height:462px">
  <div class="panel-tan" style="width:325px"></div>
  <svg class="deco" viewBox="0 0 648 462">
    <polyline points="0,128 135,50 135,0" fill="none" stroke="var(--tan-light)" stroke-width="10"/>
    <polygon points="366,0 366,42 432,84 499,42 499,0" fill="var(--tan)"/>
    <polyline points="246,0 246,50 329,92 412,50 412,0" fill="none" stroke="var(--ink)" stroke-width="1.6"/>
    <polygon points="438,462 438,438 542,362 648,438 648,462" fill="var(--tan)"/>
    <polyline points="528,462 528,426 603,368 648,398" fill="none" stroke="var(--ink)" stroke-width="1.6"/>
  </svg>
  <div class="brand" style="left:383px;top:147px;width:200px">
    <span class="mark" style="width:44px;height:44px"></span>
    <span class="name" style="font-size:18px">BRAMBLEWICK</span>
    <span class="sub" style="font-size:12px">HOMES</span>
    <span style="display:block;font-family:'Lato',sans-serif;font-size:7px;letter-spacing:1.4px;margin-top:10px">www.bramblewickhomestarrow.com</span>
    <span style="display:block;width:74px;height:1.5px;background:var(--rule);margin:3px auto 0"></span>
  </div>
  <div class="brand" style="left:62px;top:218px;width:200px">
    <span class="mark" style="width:24px;height:24px;margin-bottom:3px"></span>
    <span class="name" style="font-size:11px">BRAMBLEWICK</span>
    <span class="sub" style="font-size:8px;letter-spacing:2.5px">HOMES</span>
  </div>
  <ul class="contact" style="left:42px;top:280px;width:246px">
    <li><svg viewBox="0 0 10 10"><path d="M2 1l2 2-1 1.5c.8 1.4 1.6 2.2 3 3L7.5 6l2 2-1.5 1.5C4 9 1 6 .5 2z" fill="#fff"/></svg>555-014-0123</li>
    <li><svg viewBox="0 0 10 10"><rect x="1" y="3" width="8" height="5" fill="#fff"/><rect x="3" y="1" width="4" height="2" fill="#fff"/></svg>555-014-0155</li>
    <li><svg viewBox="0 0 10 10"><circle cx="5" cy="5" r="4" fill="#fff"/></svg>www.bramblewickhomestarrow.com</li>
    <li><svg viewBox="0 0 10 10"><rect x="1" y="2" width="8" height="6" fill="#fff"/><polyline points="1,2 5,5.5 9,2" fill="none" stroke="var(--tan)"/></svg>info@bramblewickhomestarrow.com</li>
    <li><svg viewBox="0 0 10 10"><path d="M5 10L2 5a3 3 0 1 1 6 0z" fill="#fff"/></svg>48 HOLLOW LANE RD. TARROW-ON-THE-LAKE, ONTARIO, K0A 2B0</li>
    <li class="socials"><span></span><span></span></li>
  </ul>
</section>

<!-- Back -->
<section class="sheet back" style="left:54px;top:666px;width:655px;height:465px">
  <div class="panel-tan" style="width:329px"></div>
  <svg class="deco" viewBox="0 0 655 465">
    <polygon points="32,465 32,422 96,382 158,422 158,465" fill="var(--tan-light)"/>
    <polyline points="0,358 96,422 96,465" fill="none" stroke="var(--ink)" stroke-width="1.6"/>
    <path d="M329,465 V375 Q329,337 367,337 H655 V465 Z" fill="var(--ink)"/>
    <polygon points="515,337 515,374 586,422 655,374 655,337" fill="var(--tan)"/>
    <polyline points="591,337 591,374 649,414 655,409" fill="none" stroke="#fff" stroke-width="1.6"/>
    <line x1="356" y1="389" x2="366" y2="381" stroke="var(--tan)" stroke-width="2"/>
    <line x1="490" y1="445" x2="500" y2="437" stroke="var(--tan)" stroke-width="2"/>
  </svg>
  <p class="letter">Welcome to the new vision of home building in Tarrow. For too long, the building and development business has been saddled with a poor image. Cost overruns, missed deadlines, and poor workmanship has led to most consumers feeling uneasy on building a new home. Unfortunately, in most cases, this image is warranted.<br>When we started The Bramblewick Group in 1992, we vowed do our utmost to dispel the industry of this negative rap. We wanted to make honesty, solid workmanship, and above all, excellent service our hallmarks.<br>Quite often, the language used by builders to describe their homes can be difficult for consumers to understand. At Bramblewick Homes, we value the opportunity to sit down with each and every client to explain any confusing terminology, as well as absorb as much input as we can from you, the purchaser. Furthermore, this ensures that there are no misconceptions or misunderstandings that exist between us and our clients before executing any contract. We go to great lengths to maintain our hallmarks and to ensure that we have nothing but satisfied customers.<br>There couldn't be a better time to build a new home in the Tarrow Region. Industries are booming, and the beautiful landscape this region has to offer has led to new citizens flocking down here in recent years. From the wineries and restaurants to the picturesque views and kind neighbors, the region of Tarrow has become a desirable spot for families of all types.<br>The time is now to make your dreams a reality. We look forward to the opportunity to build your dream home in the near future, and if you have any questions, please do not hesitate to ask myself, or a member of my staff.</p>
  <div class="signoff">Yours truly,<br><br>Marten Hollis<br>Founder and President</div>
  <div class="brand" style="left:214px;top:334px;width:80px">
    <span class="mark" style="width:20px;height:20px;margin-bottom:2px"></span>
    <span class="name" style="font-size:6px">BRAMBLEWICK</span>
    <span class="sub" style="font-size:4.5px;letter-spacing:1.5px">HOMES</span>
  </div>
  <ul class="back-contact">
    <li><svg viewBox="0 0 10 10"><path d="M2 1l2 2-1 1.5c.8 1.4 1.6 2.2 3 3L7.5 6l2 2-1.5 1.5C4 9 1 6 .5 2z" fill="#fff"/></svg>555-014-0123</li>
    <li><svg viewBox="0 0 10 10"><rect x="1" y="3" width="8" height="5" fill="#fff"/><rect x="3" y="1" width="4" height="2" fill="#fff"/></svg>555-014-0155</li>
    <li><svg viewBox="0 0 10 10"><circle cx="5" cy="5" r="4" fill="#fff"/></svg>www.bramblewickhomestarrow.com</li>
    <li style="line-height:9px;font-weight:700"><svg viewBox="0 0 10 10" style="margin-top:1px"><path d="M5 10L2 5a3 3 0 1 1 6 0z" fill="#fff"/></svg>48 HOLLOW LANE RD. TARROW-ON-<br>THE-LAKE, ONTARIO, K0A 2B0</li>
  </ul>
  <div class="pocket-card">your business card goes here</div>
</section>

<!-- Inside -->
<section class="sheet inside" style="left:808px;top:676px;width:323px;height:454px">
  <svg class="deco" viewBox="0 0 323 454">
    <polygon points="0,454 0,424 165,344 323,404 323,454" fill="var(--tan)"/>
    <polyline points="194,454 194,392 270,324 323,364" fill="none" stroke="var(--ink)" stroke-width="1.4"/>
  </svg>
  <div class="brand" style="left:111px;top:24px;width:100px">
    <span class="mark" style="width:42px;height:42px;margin-bottom:4px"></span>
    <span class="name" style="font-size:9.5px">BRAMBLEWICK</span>
    <span class="sub" style="font-size:7px;letter-spacing:2.4px">HOMES</span>
  </div>
  <h1 class="profile-title"><b>Corporate</b> <span>Profile</span></h1>
  <div class="profile-body">
    <strong>Dear Sir/Madam:</strong>
    At Bramblewick Homes (Tarrow), we believe that there is only one way to build a new home: with pride in every detail and careful workmanship. Honest quality is hard to find, yet our team is committed to changing that. From starter homes to custom builds, we construct each one as if it were our own.<br>
    We use only sound materials and hire skilled, dedicated trades so that every house is given our full attention to quality. We take such care because we want to be proud of each home we build, just as proud as you will be living in it.<br>
    Beginning in 1992 and stretching over two family generations, the Bramblewick Group has left a quality product in nearly every corner of the Tarrow Region. From our early work to our recent homes, the results speak for themselves. Over the coming years our work will lead us into new towns across the province, creating a new age of home building in the region.<br>
    Building fine homes has been a passion this family has kept for decades. Visit our website for details on current and future developments, where you will find a wide range of elevations and floor plans we update so each client can find a home that meets their tastes and needs.
  </div>
  <ul class="inside-contact">
    <li><svg viewBox="0 0 10 10"><path d="M2 1l2 2-1 1.5c.8 1.4 1.6 2.2 3 3L7.5 6l2 2-1.5 1.5C4 9 1 6 .5 2z" fill="#333"/></svg>555-014-0123</li>
    <li><svg viewBox="0 0 10 10"><rect x="1" y="3" width="8" height="5" fill="#333"/><rect x="3" y="1" width="4" height="2" fill="#333"/></svg>555-014-0155</li>
    <li><svg viewBox="0 0 10 10"><circle cx="5" cy="5" r="4" fill="#333"/></svg>www.bramblewickhomestarrow.com</li>
    <li style="line-height:6px"><svg viewBox="0 0 10 10"><path d="M5 10L2 5a3 3 0 1 1 6 0z" fill="#333"/></svg>48 HOLLOW LANE RD. TARROW-ON-THE-LAKE,<br>ONTARIO, K0A 2B0</li>
  </ul>
</section>

</body>
</html>
```